Local Flower Farm Needs Business Card Design

I need business cards designed for a flower farm based in Eudora, Kansas.
Business Info:
We are a local cut flower farm located in Eudora, Kansas, founded by Corinne Haldwick. What started as a passion for agriculture and search for more joy in daily life has blossomed into a small business dedicated to providing the community with beautiful, fresh, and sustainable flowers. We specialize in local, seasonal blooms, ensuring that every petal reflects the care and dedication we pour into our craft. Our mission is to deliver the highest quality flowers directly to our customers through local farmers markets and to florists who share our commitment to sustainability. Join us in celebrating the beauty of nature, one bloom at a time!
Contact Details:
Corinne Haldwick
Owner
Phone 913-555-0147
Facebook: Rosalind Thorpe Gardens
Instagram: @RosalindThorpeGardens
Website: RosalindThorpeGardens.example
Target Market(s)
Wholesale to Florists and Direct to Consumer via Farmers Market
Industry/Entity Type
Florist, Farm
Contact Information for Business Card
Name, Contact Info, Logo
Look and feel
Each slider illustrates characteristics of the customer's brand and the style your logo design should communicate.

```html
<!DOCTYPE html>
<html lang="en">
<head>
<meta charset="utf-8">
<title>Rosalind Thorpe Gardens – Business Card</title>
<link href="https://fonts.googleapis.com/css2?family=Tinos:wght@400;700&display=swap" rel="stylesheet">
<style>
  :root {
    --page: #e2e6e8;
    --ink: #0b2a2f;
    --paper: #ffffff;
    --glow: 150, 211, 155;
    --text: #111111;
  }
  * { margin: 0; padding: 0; box-sizing: border-box; }
  html, body { width: 1200px; height: 960px; overflow: hidden; }
  body { background: var(--page); font-family: "Tinos", "Times New Roman", serif; position: relative; }

  .card { position: absolute; left: 247px; width: 706px; height: 403px; overflow: hidden; }
  .card--front { top: 58px; background: var(--ink); }
  .card--back { top: 500px; background: var(--paper); }

  .front__glow {
    position: absolute; left: 0; top: 0; width: 706px; height: 403px;
    background:
      radial-gradient(ellipse 150px 190px at 270px 0px, rgba(var(--glow), 0.95), rgba(var(--glow), 0.55) 45%, rgba(var(--glow), 0) 100%),
      radial-gradient(ellipse 330px 260px at 200px 0px, rgba(var(--glow), 0.35), rgba(var(--glow), 0) 100%),
      radial-gradient(ellipse 300px 420px at 190px 120px, rgba(40, 90, 90, 0.35), rgba(11, 42, 47, 0) 100%);
  }

  .badge {
    position: absolute; border-radius: 50%;
    display: flex; flex-direction: column; align-items: center; justify-content: center;
    text-align: center; letter-spacing: 2px; text-transform: uppercase; font-weight: 400;
  }
  .badge--front { left: 502px; top: 204px; width: 176px; height: 176px; border: 1px solid var(--paper); color: var(--paper); font-size: 15px; line-height: 1.5; }
  .badge--back { left: 81px; top: 102px; width: 194px; height: 194px; border: 1px solid var(--ink); color: var(--ink); font-size: 17px; line-height: 1.5; }

  .divider { position: absolute; left: 350px; top: 99px; width: 1.5px; height: 203px; background: var(--ink); }

  .contact { position: absolute; left: 391px; top: 132px; color: var(--text); }
  .contact__name { font-size: 35px; font-weight: 700; letter-spacing: 0.6px; line-height: 1; }
  .contact__role { font-size: 17px; margin-top: 3px; letter-spacing: 0.5px; }
  .contact__list { list-style: none; margin-top: 20px; }
  .contact__item { display: flex; align-items: center; gap: 9px; font-size: 18px; line-height: 24px; letter-spacing: 0.3px; }
  .contact__icon { width: 16px; height: 16px; flex: none; }

  .social-band {
    position: absolute; left: 0; top: 356px; width: 706px; height: 24px; background: var(--ink);
    color: var(--paper); font-size: 17px; letter-spacing: 0.3px;
  }
  .social { position: absolute; top: 0; height: 24px; display: flex; align-items: center; gap: 8px; }
  .social--facebook { left: 32px; }
  .social--instagram { left: 410px; }
  .social__dot { width: 16px; height: 16px; border-radius: 50%; background: var(--paper); }
  .social__square { width: 16px; height: 16px; border: 2px solid var(--paper); border-radius: 4px; }
  .band__mark {
    position: absolute; left: 338px; top: -8px; width: 40px; height: 40px; border-radius: 50%;
    background: var(--paper); border: 2px solid var(--ink);
  }
</style>
</head>
<body>
  <section class="card card--front">
    <div class="front__glow" role="img" aria-label="Soft green light falling over a large embossed botanical monogram decoration"></div>
    <div class="badge badge--front"><span>Rosalind</span><span>Thorpe</span><span>Gardens</span></div>
  </section>

  <section class="card card--back">
    <div class="badge badge--back"><span>Rosalind</span><span>Thorpe</span><span>Gardens</span></div>
    <div class="divider"></div>

    <div class="contact">
      <h1 class="contact__name">Corinne Haldwick</h1>
      <p class="contact__role">Owner</p>
      <ul class="contact__list">
        <li class="contact__item">
          <svg class="contact__icon" viewBox="0 0 24 24" aria-hidden="true"><path fill="#0b2a2f" d="M6.6 10.8a15.1 15.1 0 0 0 6.6 6.6l2.2-2.2c.3-.3.7-.4 1-.2 1.1.4 2.3.6 3.6.6.6 0 1 .4 1 1V20c0 .6-.4 1-1 1A17 17 0 0 1 3 4c0-.6.4-1 1-1h3.5c.6 0 1 .4 1 1 0 1.3.2 2.5.6 3.6.1.3 0 .7-.2 1z"/><path fill="none" stroke="#0b2a2f" stroke-width="2" d="M14 3a7 7 0 0 1 7 7M14 7a3 3 0 0 1 3 3"/></svg>
          <span>913-555-0147</span>
        </li>
        <li class="contact__item">
          <svg class="contact__icon" viewBox="0 0 24 24" aria-hidden="true"><circle cx="12" cy="12" r="10" fill="#0b2a2f"/><path fill="none" stroke="#fff" stroke-width="1.4" d="M2 12h20M12 2c3 3 3 17 0 20M12 2c-3 3-3 17 0 20"/></svg>
          <span>RosalindThorpeGardens.example</span>
        </li>
      </ul>
    </div>

    <div class="social-band">
      <div class="social social--facebook"><span class="social__dot"></span><span>Rosalind Thorpe Gardens</span></div>
      <div class="band__mark"></div>
      <div class="social social--instagram"><span class="social__square"></span><span>@RosalindThorpeGardens</span></div>
    </div>
  </section>
</body>
</html>
```